Dalvick's Business Card

I need some designs for a new business card including the new logo attached. An old example of our business card is also attached to show all the data that should be included on the new design.
**I added some more examples someone had mocked up**

Contact Information for Business Card

Should include all info on other examples uploaded.

```html
<!DOCTYPE html>
<html lang="en">
<head>
<meta charset="utf-8">
<title>Dalvick's Business Card</title>
<link href="https://fonts.googleapis.com/css2?family=Montserrat:wght@700;800&family=Poppins:wght@400;700&display=swap" rel="stylesheet">
<style>
  :root {
    --brand-blue: #0a70c0;
    --brand-red: #e31c25;
    --card-white: #ffffff;
    --ink: #1b1b1b;
    --rule: #c9c9c9;
    --backdrop: #e9ebee;
  }
  * { box-sizing: border-box; margin: 0; padding: 0; }
  html, body { width: 1200px; height: 900px; overflow: hidden; }
  body { background: var(--backdrop); position: relative; font-family: "Poppins", sans-serif; }

  .card {
    position: absolute;
    width: 560px;
    height: 320px;
    border-radius: 4px;
    overflow: hidden;
    box-shadow: 0 10px 24px rgba(0,0,0,.18);
  }

  /* Front */
  .card--front {
    left: 110px; top: 90px;
    background: var(--brand-blue);
    color: var(--card-white);
    display: flex; flex-direction: column; align-items: center; justify-content: center;
    gap: 42px;
  }
  .brand { display: flex; align-items: center; gap: 16px; }
  .brand__dot { width: 54px; height: 54px; border-radius: 50%; background: var(--card-white); }
  .brand__name {
    font-family: "Montserrat", sans-serif; font-weight: 800;
    font-size: 50px; letter-spacing: 1px; color: var(--card-white);
  }
  .front__tagline {
    font-family: "Montserrat", sans-serif; font-weight: 700;
    font-size: 19px; line-height: 1.35; text-align: center; text-transform: uppercase; letter-spacing: .5px;
  }

  /* Back */
  .card--back { left: 530px; top: 490px; background: var(--card-white); }
  .back__wave { position: absolute; inset: 0; width: 100%; height: 100%; }
  .back__brand {
    position: absolute; left: 40px; top: 70px; width: 200px;
    display: flex; flex-direction: column; align-items: center; gap: 12px;
  }
  .back__brand .brand__dot { width: 60px; height: 60px; background: var(--brand-blue); }
  .back__brand .brand__name { font-size: 32px; color: var(--brand-blue); }
  .back__divider {
    position: absolute; left: 258px; top: 40px; width: 1px; height: 130px; background: var(--rule);
  }
  .contact { position: absolute; left: 280px; top: 30px; }
  .contact__name {
    font-family: "Montserrat", sans-serif; font-weight: 800;
    color: var(--brand-blue); font-size: 21px; margin-bottom: 8px;
  }
  .contact__line { display: flex; align-items: center; gap: 8px; font-size: 12.5px; color: var(--ink); margin-bottom: 4px; }
  .contact__line svg { width: 15px; height: 15px; flex: none; }
  .contact__badge {
    font-family: "Montserrat", sans-serif; font-weight: 800; font-size: 12.5px; text-transform: uppercase;
  }
  .contact__badge--blue { color: var(--brand-blue); margin-top: 12px; }
  .contact__badge--red { color: var(--brand-red); margin-top: 3px; }
  .service-area {
    position: absolute; left: 40px; bottom: 28px;
    color: var(--card-white); font-size: 15px; line-height: 1.35;
  }
</style>
</head>
<body>

<section class="card card--front">
  <div class="brand">
    <span class="brand__dot"></span>
    <span class="brand__name">DALVICK'S</span>
  </div>
  <p class="front__tagline">Call today for all your HVAC<br>refrigeration &amp; plumbing needs</p>
</section>

<section class="card card--back">
  <svg class="back__wave" viewBox="0 0 560 320" preserveAspectRatio="none" aria-hidden="true">
    <path d="M0 250 C150 214 320 204 420 190 C490 180 535 162 560 148 L560 320 L0 320 Z" fill="var(--brand-blue)"/>
    <path d="M225 200 C360 194 480 176 560 124 L560 142 C480 184 370 198 225 200 Z" fill="var(--brand-red)"/>
  </svg>

  <div class="back__brand">
    <span class="brand__dot"></span>
    <span class="brand__name">DALVICK'S</span>
  </div>

  <div class="back__divider"></div>

  <div class="contact">
    <p class="contact__name">MARK DALVICK</p>
    <p class="contact__line">
      <svg viewBox="0 0 24 24" aria-hidden="true"><path fill="var(--brand-red)" d="M6.6 10.8a15.1 15.1 0 0 0 6.6 6.6l2.2-2.2c.3-.3.7-.4 1-.2 1.1.4 2.3.6 3.6.6.6 0 1 .4 1 1V20c0 .6-.4 1-1 1A17 17 0 0 1 3 4c0-.6.4-1 1-1h3.5c.6 0 1 .4 1 1 0 1.3.2 2.5.6 3.6.1.3 0 .7-.2 1z"/></svg>
      555.014.2290
    </p>
    <p class="contact__line">
      <svg viewBox="0 0 24 24" aria-hidden="true"><path fill="var(--brand-red)" d="M2 5h20v14H2z"/><path fill="none" stroke="#fff" stroke-width="1.6" d="M2 5l10 8 10-8"/></svg>
      hvacdalvick@example.com
    </p>
    <p class="contact__badge contact__badge--blue">Licensed &amp; Insured</p>
    <p class="contact__badge contact__badge--red">Family Owned &amp; Operated</p>
  </div>

  <p class="service-area">Serves Ashford,<br>IA &amp; Surrounding Areas</p>
</section>

</body>
</html>
```